UI Design for a pre-ordering & Universal loyalty mobile app

We have built a central universal, preordering and gamification mobile app for alot of F&B merchant. The app is called PYRK (Pyrick as in eating something fast). Main goal for this app is too
1. Give users a universal loyalty system where they can accumulate loyalty points and use it on any brands
2. Gives user the ability to preorder for their food or drinks on the app and pick it up instore
3. There will be an E-wallet that is general or there can be a brand e-wallet (where they top-up with the brand only and get extra bonus)
4. There will be promotion such as games, top-up bonuses and rewards.
5. Community app where they can send money or promotion to their friends and will be able to play games together
This app is developed on the Flutter framework and also uses fontawesome font/icon package. Please consider this when doing the UI design for the app.
We are planning to create a mascot for our app as well and when it comes to color and icon, it's not set in stone and we are open for ideas.
I will attached our app icon and a few of our screens for your reference and each page details as follows:
Navigation bar.
There is a navigation bar on the top that should be visible on all screen. On the left will be a button to enter the menu which gives user more option and on the right will be a place for them to scan their QR code for loyalty points or payment and also a button to access their e-wallet.
1. Home screen
This screen is basically the main screen after user login. In this screen there will be
- Main banner (main promotions that's controlled by us)
- Specials banner (smaller) that will be controlled by the store/brands
- Favourite Store or Favourite food/drinks that user pre-configure
2. Shop screen (or can be called something else)
This screen is where they can browse all our participating stores. This screen will include
- Categories (filter)
- Brands which user can click and only view the brand page and stores
- All stores sorted by distances
3. Brand screen
The brand screen gives our brand with multiple store a presense on the app that is branded for them. They can have their own color scheme, logo and will only display their own store
4. Store screen
This will display all the store details, opening time, location, contact information etc.
- This screen will contain a banner/store image
- Store details
- Categories
- Food/drinks within the category
5. Order history screen
This will display their current order or their past order. Not sure if it should be on the main navigation or the sub navigation.
When making the UI design, please work on a color theme that will suit and also consider a mascot design in the future.
Feel free to ask me any questions before proceeding.
Thanks

```html
<!DOCTYPE html>
<html lang="en">
<head>
<meta charset="utf-8">
<title>PYRK – App Screens</title>
<link href="https://fonts.googleapis.com/css2?family=Bebas+Neue&family=Poppins:wght@300;400;500;600&display=swap" rel="stylesheet">
<style>
:root{
  --orange:#f26a1b;
  --ink:#1d1d1f;
  --muted:#8a8a8f;
  --line:#ececec;
  --bg:#e6e6e6;
  --screen:#ffffff;
  --card:#f7f7f7;
  --tag:#b9b9b9;
}
*{box-sizing:border-box;margin:0;padding:0}
html,body{width:1200px;height:780px;overflow:hidden}
body{background:var(--bg);font-family:'Poppins',sans-serif;color:var(--ink);position:relative}
.screen{position:absolute;top:40px;width:330px;height:700px;background:var(--screen);border-radius:34px;overflow:hidden;box-shadow:0 16px 40px rgba(0,0,0,.12)}
.screen--home{left:75px}.screen--shop{left:435px}.screen--orders{left:795px}
.status{height:34px;display:flex;justify-content:space-between;align-items:center;padding:0 26px;font-size:11px}
.status__icons{display:flex;gap:4px;align-items:center}
.battery{width:18px;height:8px;background:#222;border-radius:2px;display:inline-block}
.topnav{display:flex;align-items:center;justify-content:space-between;height:78px;padding:0 24px;border-bottom:1px solid var(--line)}
.topnav__actions{display:flex;gap:14px}
.icon{width:20px;height:20px;stroke:currentColor;fill:none;stroke-width:1.6;stroke-linecap:round;stroke-linejoin:round}
.appname{display:flex;align-items:center;gap:7px}
.appname__dot{width:12px;height:12px;border-radius:50%;background:var(--orange)}
.appname__text{font-family:'Poppins',sans-serif;font-weight:600;font-size:18px;color:var(--ink);line-height:1}
.heading{font-family:'Bebas Neue',sans-serif;font-size:22px;text-align:center;letter-spacing:.3px;font-weight:400}
.hero{position:relative;height:170px;background:linear-gradient(100deg,#c9a37a 0%,#f1e3d0 45%,#f5efe8 100%)}
.hero__photo{position:absolute;left:30px;top:10px;width:110px;height:155px;border-radius:14px;background:linear-gradient(160deg,#6d4b3a,#d27a3a 50%,#2a2a2a)}
.hero__copy{position:absolute;left:165px;top:52px;font-family:'Bebas Neue',sans-serif;font-size:17px;line-height:1.45;color:#333}
.pill{display:inline-block;background:var(--orange);color:#fff;border-radius:20px;font-size:7px;font-family:'Poppins',sans-serif;font-weight:600;padding:4px 12px;margin-top:8px}
.deals{display:flex;align-items:center;justify-content:center;gap:12px;margin-top:10px}
.deal{width:124px;height:62px;border-radius:4px}
.deal--coco{background:linear-gradient(90deg,#7fc53b,#e7d22a 50%,#d8232a)}
.deal--coffee{background:linear-gradient(90deg,#8b1b1b,#3a1c12)}
.arrow{width:10px;height:10px;stroke:var(--muted)}
.fav{position:relative;margin:10px 28px 0;height:132px;background:linear-gradient(180deg,#4f5a58,#2b2622 60%,#5a4433)}
.fav__badges{position:absolute;right:10px;top:10px;display:flex;gap:4px}
.fav__badge{width:18px;height:18px;border-radius:50%;background:var(--orange)}
.tabbar{position:absolute;left:0;right:0;bottom:0;height:62px;background:#fff;display:flex;justify-content:space-around;align-items:center;padding-bottom:8px}
.tabbar .icon{width:26px;height:26px;stroke-width:1.4;color:#222}
.tabbar .is-active{color:var(--orange)}
.search{margin:14px 22px 0;height:42px;border-radius:22px;box-shadow:0 2px 10px rgba(0,0,0,.08);display:flex;align-items:center;justify-content:space-between;padding:0 4px 0 18px;font-size:12px;color:#aaa;font-weight:300}
.search__btn{width:34px;height:34px;border-radius:50%;background:var(--orange);display:flex;align-items:center;justify-content:center;color:#fff}
.categories{display:flex;justify-content:space-between;padding:0 18px;margin-top:10px}
.category{display:flex;flex-direction:column;align-items:center;gap:8px;font-size:11px;width:70px}
.category__ring{width:44px;height:44px;border-radius:50%;border:1px solid #ddd;display:flex;align-items:center;justify-content:center;color:var(--orange)}
.brands{display:flex;align-items:center;gap:10px;padding:0 22px;margin-top:34px}
.brands .heading{margin-right:24px}
.brand-tile{width:34px;height:34px;border-radius:4px}
.store{display:flex;gap:14px;margin:12px 22px 0;padding:4px;box-shadow:0 2px 10px rgba(0,0,0,.08);border-radius:4px}
.store__photo{width:92px;height:102px;flex:none;background:linear-gradient(160deg,#d9c3a8,#8a5a3a 60%,#3b2a20)}
.store__info{padding-top:8px;font-size:9px;color:var(--muted);font-weight:300;line-height:1.9}
.store__name{font-size:12px;color:var(--ink);font-weight:400}
.row{display:flex;align-items:center;gap:4px}
.row .icon{width:9px;height:9px;color:var(--orange);stroke-width:2}
.tabs{display:flex;justify-content:center;gap:6px;margin-top:14px}
.tab{width:92px;height:32px;border-radius:18px;border:1px solid var(--orange);display:flex;align-items:center;justify-content:center;font-size:11px;font-weight:500;color:#1f3c88}
.tab.is-active{background:var(--orange);color:#fff}
.order{margin:14px 18px 0;background:var(--card);padding:8px 8px 6px;border-radius:3px}
.order__top{display:flex;gap:10px;padding-bottom:8px;border-bottom:1px solid var(--line)}
.order__photo{width:52px;height:46px;flex:none;background:linear-gradient(180deg,#55605d,#2b2622 60%,#5a4433)}
.order__text{flex:1;max-width:128px;font-size:9px;font-weight:500;line-height:1.6}
.order__loc{font-size:7px;font-weight:400;color:#555;margin-top:4px}
.order__side{margin-left:auto;display:flex;flex-direction:column;align-items:flex-end;gap:12px}
.tag{background:var(--tag);color:#fff;font-size:6px;padding:2px 6px;border-radius:2px}
.link{font-size:9px;color:var(--orange)}
.order__meta{display:flex;justify-content:space-between;align-items:center;padding:8px 2px;border-bottom:1px solid var(--line);font-size:8px;color:var(--muted)}
.price{font-size:10px;font-weight:600;color:var(--ink)}
.order__rate{display:flex;justify-content:space-between;align-items:center;padding:6px 2px 0;font-size:10px}
.stars{color:#f6a31a;font-size:9px;letter-spacing:1px;margin-left:6px}
.btn-small{background:var(--orange);color:#fff;font-size:5.5px;font-weight:600;padding:5px 8px;border-radius:10px}
</style>
</head>
<body>
<svg width="0" height="0" style="position:absolute">
  <defs>
    <symbol id="i-menu" viewBox="0 0 24 24"><path d="M4 6h16M4 12h16M4 18h16"/></symbol>
    <symbol id="i-scan" viewBox="0 0 24 24"><path d="M4 8V4h4M16 4h4v4M20 16v4h-4M8 20H4v-4M8 12h8"/></symbol>
    <symbol id="i-wallet" viewBox="0 0 24 24"><path d="M4 8h15a1 1 0 0 1 1 1v10H4zM4 8l11-4 1 4M15 13h5"/></symbol>
    <symbol id="i-home" viewBox="0 0 24 24"><path d="M3 11l9-8 9 8M5 9v11h5v-6h4v6h5V9"/></symbol>
    <symbol id="i-gift" viewBox="0 0 24 24"><path d="M3 8h18v4H3zM5 12v9h14v-9M12 8v13M12 8c-2-4-6-4-6-1s6 1 6 1c2-4 6-4 6-1s-6 1-6 1"/></symbol>
    <symbol id="i-orders" viewBox="0 0 24 24"><path d="M15 11V3H5v18h8M8 7h4M8 11h4M8 15h3"/><circle cx="17" cy="17" r="4"/><path d="M15.3 17l1.2 1.2 2.2-2.2"/></symbol>
    <symbol id="i-grid" viewBox="0 0 24 24"><rect x="3" y="3" width="7" height="7" rx="1.5"/><rect x="14" y="3" width="7" height="7" rx="1.5"/><rect x="3" y="14" width="7" height="7" rx="1.5"/><rect x="14" y="14" width="7" height="7" rx="1.5"/></symbol>
    <symbol id="i-search" viewBox="0 0 24 24"><circle cx="11" cy="11" r="6"/><path d="M20 20l-4.5-4.5"/></symbol>
    <symbol id="i-pin" viewBox="0 0 24 24"><path d="M12 21s-6-6-6-11a6 6 0 0 1 12 0c0 5-6 11-6 11z"/><circle cx="12" cy="10" r="2"/></symbol>
    <symbol id="i-phone" viewBox="0 0 24 24"><path d="M5 3h4l2 5-3 2a11 11 0 0 0 6 6l2-3 5 2v4a2 2 0 0 1-2 2A17 17 0 0 1 3 5a2 2 0 0 1 2-2z"/></symbol>
    <symbol id="i-clock" viewBox="0 0 24 24"><circle cx="12" cy="12" r="9"/><path d="M12 7v5l3 2"/></symbol>
    <symbol id="i-ring" viewBox="0 0 24 24"><circle cx="12" cy="12" r="7"/></symbol>
    <symbol id="i-cup" viewBox="0 0 24 24"><path d="M4 11h13v2a6 6 0 0 1-6 6h-1a6 6 0 0 1-6-6zM17 12h2a2 2 0 0 1 0 4h-3M9 4c-1 2 1 3 0 5M13 4c-1 2 1 3 0 5"/></symbol>
    <symbol id="i-boba" viewBox="0 0 24 24"><path d="M7 8h10l-1.5 13h-7zM12 8l2-6M9 16h.1M12 17h.1M15 16h.1"/></symbol>
    <symbol id="i-coffee" viewBox="0 0 24 24"><path d="M6 7h12l-1.5 14h-9zM5 4h14v3H5zM9 13h6"/></symbol>
    <symbol id="i-snack" viewBox="0 0 24 24"><path d="M5 20l3-12h8l3 12zM8 8l1-4M12 8V3M16 8l-1-4"/></symbol>
    <symbol id="i-chev-l" viewBox="0 0 24 24"><path d="M15 5l-7 7 7 7"/></symbol>
    <symbol id="i-chev-r" viewBox="0 0 24 24"><path d="M9 5l7 7-7 7"/></symbol>
    <symbol id="i-signal" viewBox="0 0 30 12"><path d="M1 11v-2M6 11V7M11 11V4M16 11V1" stroke-width="2.4"/><path d="M21 5a6 6 0 0 1 8 0M23 8a3 3 0 0 1 4 0" stroke-width="1.6"/></symbol>
  </defs>
</svg>

<!-- Home -->
<section class="screen screen--home">
  <div class="status"><span>9:30</span><span class="status__icons"><svg class="icon" style="width:30px;height:12px" viewBox="0 0 30 12"><use href="#i-signal"/></svg><span class="battery"></span></span></div>
  <header class="topnav">
    <svg class="icon"><use href="#i-menu"/></svg>
    <div class="appname"><span class="appname__dot"></span><span class="appname__text">PYRK</span></div>
    <div class="topnav__actions"><svg class="icon"><use href="#i-scan"/></svg><svg class="icon"><use href="#i-wallet"/></svg></div>
  </header>
  <div class="hero">
    <div class="hero__photo" role="img" aria-label="Phone with food and a frying pan bursting out of the screen"></div>
    <div class="hero__copy">PREORDERING AND<br>GAMIFICATION MOBILE APP<br><span class="pill">ORDER NOW</span></div>
  </div>
  <h2 class="heading" style="margin-top:10px">DEALS</h2>
  <div class="deals">
    <svg class="icon arrow"><use href="#i-chev-l"/></svg>
    <div class="deal deal--coco" role="img" aria-label="Coconut jelly and boba promotion banner"></div>
    <div class="deal deal--coffee" role="img" aria-label="Free coffee promotion banner from Daily Roast"></div>
    <svg class="icon arrow" style="stroke:#222"><use href="#i-chev-r"/></svg>
  </div>
  <h2 class="heading" style="margin-top:14px">FAVOURITES</h2>
  <div class="fav" role="img" aria-label="Restaurant interior with set tables">
    <div class="fav__badges"><span class="fav__badge"></span><span class="fav__badge"></span></div>
  </div>
  <nav class="tabbar">
    <svg class="icon is-active"><use href="#i-home"/></svg>
    <svg class="icon"><use href="#i-gift"/></svg>
    <svg class="icon"><use href="#i-orders"/></svg>
    <svg class="icon"><use href="#i-grid"/></svg>
  </nav>
</section>

<!-- Shop -->
<section class="screen screen--shop">
  <div class="status"><span>9:30</span><span class="status__icons"><svg class="icon" style="width:30px;height:12px" viewBox="0 0 30 12"><use href="#i-signal"/></svg><span class="battery"></span></span></div>
  <header class="topnav">
    <svg class="icon"><use href="#i-menu"/></svg>
    <div class="appname"><span class="appname__dot"></span><span class="appname__text">PYRK</span></div>
    <div class="topnav__actions"><svg class="icon"><use href="#i-scan"/></svg><svg class="icon"><use href="#i-wallet"/></svg></div>
  </header>
  <div class="search"><span>Search</span><span class="search__btn"><svg class="icon" style="width:16px;height:16px"><use href="#i-search"/></svg></span></div>
  <h2 class="heading" style="margin-top:14px">CATEGORIES</h2>
  <div class="categories">
    <div class="category"><span class="category__ring"><svg class="icon"><use href="#i-cup"/></svg></span>Tea</div>
    <div class="category"><span class="category__ring"><svg class="icon"><use href="#i-boba"/></svg></span>Bubble Tea</div>
    <div class="category"><span class="category__ring"><svg class="icon"><use href="#i-coffee"/></svg></span>Coffee</div>
    <div class="category"><span class="category__ring"><svg class="icon"><use href="#i-snack"/></svg></span>Snack</div>
  </div>
  <div class="brands">
    <h2 class="heading">BRAND</h2>
    <span class="brand-tile" style="background:#1d5aa8"></span>
    <span class="brand-tile" style="background:#23337a"></span>
    <span class="brand-tile" style="background:#5fae3a"></span>
    <span class="brand-tile" style="background:#1f8a4c"></span>
  </div>
  <h2 class="heading" style="margin-top:34px">STORES NEAR YOU</h2>
  <article class="store">
    <div class="store__photo" role="img" aria-label="Cafe counter interior"></div>
    <div class="store__info">
      <div class="store__name">Demo 2 Perth</div>
      <div class="row"><svg class="icon"><use href="#i-pin"/></svg>123 A Street Somewhere Here</div>
      <div class="row" style="font-size:7.5px;gap:10px"><span class="row"><svg class="icon"><use href="#i-ring"/></svg>Tea</span><span class="row"><svg class="icon"><use href="#i-ring"/></svg>Bubble Tea</span><span class="row"><svg class="icon"><use href="#i-ring"/></svg>Burgers</span></div>
      <div class="row"><svg class="icon"><use href="#i-phone"/></svg>+1 (555) 010 0199</div>
      <div class="row" style="gap:14px"><span class="row"><svg class="icon" style="color:var(--muted)"><use href="#i-clock"/></svg>5 mins</span><span class="row"><svg class="icon" style="color:var(--muted)"><use href="#i-pin"/></svg>1.24 km</span></div>
    </div>
  </article>
  <article class="store">
    <div class="store__photo" role="img" aria-label="Tea shop storefront"></div>
    <div class="store__info">
      <div class="store__name">Leafbrew Mt Lawley</div>
      <div class="row"><svg class="icon"><use href="#i-pin"/></svg>Unit 12/48 Harbour Rd Mount</div>
    </div>
  </article>
  <nav class="tabbar">
    <svg class="icon"><use href="#i-home"/></svg>
    <svg class="icon is-active"><use href="#i-gift"/></svg>
    <svg class="icon"><use href="#i-orders"/></svg>
    <svg class="icon"><use href="#i-grid"/></svg>
  </nav>
</section>

<!-- Order history -->
<section class="screen screen--orders">
  <div class="status"><span>9:30</span><span class="status__icons"><svg class="icon" style="width:30px;height:12px" viewBox="0 0 30 12"><use href="#i-signal"/></svg><span class="battery"></span></span></div>
  <h1 class="heading" style="margin-top:44px;font-size:24px">ORDER HISTORY</h1>
  <div class="tabs"><span class="tab">Queue</span><span class="tab is-active">Completed</span></div>
  <div class="search" style="margin:14px 18px 0;padding-left:16px;font-size:11px">Search by Restaurant</div>

  <article class="order">
    <div class="order__top">
      <div class="order__photo" role="img" aria-label="Restaurant interior"></div>
      <div class="order__text">Lorem ipsum dolor sit consectetur<div class="order__loc row"><svg class="icon" style="width:8px;height:8px;color:#333"><use href="#i-pin"/></svg>Lorem ipsum dolor sit</div></div>
      <div class="order__side"><span class="tag">Delivered</span><span class="link">View menu</span></div>
    </div>
    <div class="order__meta"><span>03 Oct 2023 at 2:33PM</span><span class="price">$263.50</span></div>
    <div class="order__rate"><span>Rate<span class="stars">★★★★★</span></span><span class="btn-small">Order Now</span></div>
  </article>

  <article class="order">
    <div class="order__top">
      <div class="order__photo" role="img" aria-label="Restaurant interior"></div>
      <div class="order__text">Lorem ipsum dolor sit consectetur<div class="order__loc row"><svg class="icon" style="width:8px;height:8px;color:#333"><use href="#i-pin"/></svg>Lorem ipsum dolor sit</div></div>
      <div class="order__side"><span class="tag">Delivered</span><span class="link">View menu</span></div>
    </div>
    <div class="order__meta"><span>03 Oct 2023 at 2:33PM</span><span class="price">$263.50</span></div>
    <div class="order__rate"><span>Rate<span class="stars">★★★★★</span></span><span class="btn-small">Order Now</span></div>
  </article>

  <article class="order">
    <div class="order__top">
      <div class="order__photo" role="img" aria-label="Restaurant interior"></div>
      <div class="order__text">Lorem ipsum dolor sit consectetur<div class="order__loc row"><svg class="icon" style="width:8px;height:8px;color:#333"><use href="#i-pin"/></svg>Lorem ipsum dolor sit</div></div>
      <div class="order__side"><span class="tag">Delivered</span><span class="link">View menu</span></div>
    </div>
  </article>

  <nav class="tabbar">
    <svg class="icon"><use href="#i-home"/></svg>
    <svg class="icon"><use href="#i-gift"/></svg>
    <svg class="icon is-active"><use href="#i-orders"/></svg>
    <svg class="icon"><use href="#i-grid"/></svg>
  </nav>
</section>
</body>
</html>
```